Fresh Dwelling Tract Guide needs a new Landing Page

I like to get a landing page or website with 2-3 pages to help target home buyers who are looking to buy homes from builders such as TW Residences, Morvik, P.L. Fennick, etc. The landing page/website to be non-cluttered and be able to explain to home buyers that there are many benefits to include me as their buyer's agent when they buy a brand new home from any builders.
I may want to incorporate a short explanation video (animated) on the landing page and then for the viewer to click on a button that will take them to another page where they can search for new homes from different builders.
Target Market(s)
Home buyers looking to buy brand new home from builders such as TW Residences, Morvik, P.L. Fennick, etc.
Industry/Entity Type
Real Estate
Number of Pages Required
2 page
Font styles to use
Requirements
Must have
- The landing page may have the explanation video at the bottom of the landing page (scrolled down) or there may be a CALL TO ACTION button that takes the viewer to the 2nd page to watch the explanation video. Once they watched the explanation video and are still interested, they can click on another CALL TO ACTION button that will take them to another website that they will be able to search for all the available new homes and register their contact information.
Should not have
- No clutters and no dark colors.

```html
<!DOCTYPE html>
<html lang="en">
<head>
<meta charset="utf-8">
<title>Fresh Dwelling Tract Guide</title>
<link href="https://fonts.googleapis.com/css2?family=Montserrat:wght@400;500;600&display=swap" rel="stylesheet">
<style>
  :root {
    --ink: #ffffff;
    --sky: #6d9ac4;
    --sky-soft: #8fb2d0;
    --glow: #d2aa76;
    --lawn: #86a35f;
    --drive: #a7a3b3;
    --footer: #5a7390;
    --veil: rgba(30, 50, 75, 0.16);
    --text-lift: 0 1px 6px rgba(20, 35, 55, 0.45);
  }
  * { margin: 0; padding: 0; box-sizing: border-box; }
  html, body { width: 1200px; height: 794px; overflow: hidden; }
  body {
    font-family: "Montserrat", Arial, sans-serif;
    color: var(--ink);
    background: var(--footer);
    position: relative;
  }
  .hero {
    position: absolute; left: 0; top: 0; width: 1200px; height: 730px;
  }
  .hero-photo {
    position: absolute; inset: 0;
    background:
      radial-gradient(ellipse 440px 230px at 600px 370px, rgba(236,200,140,0.55), transparent 70%),
      linear-gradient(180deg, var(--sky) 0%, var(--sky-soft) 26%, var(--glow) 52%, var(--lawn) 80%, var(--drive) 100%);
  }
  .hero-veil { position: absolute; inset: 0; background: var(--veil); }
  .brand {
    position: absolute; left: 87px; top: 47px;
    font-size: 22px; font-weight: 500; letter-spacing: 0.3px;
  }
  .menu-toggle {
    position: absolute; left: 1057px; top: 34px;
    width: 56px; height: 56px; border: 2px solid var(--ink); border-radius: 50%;
    display: flex; align-items: center; justify-content: center;
  }
  .hero-content {
    position: absolute; left: 0; right: 0; top: 322px; text-align: center;
    text-shadow: var(--text-lift);
  }
  .hero-title { font-size: 38px; font-weight: 600; line-height: 54px; }
  .hero-sub { margin-top: 14px; font-size: 16.8px; font-weight: 400; line-height: 24px; }
  .cta {
    display: inline-block; margin-top: 20px;
    width: 232px; height: 51px; line-height: 47px;
    border: 2px solid var(--ink); border-radius: 26px;
    font-size: 16.5px; font-weight: 500; color: var(--ink); text-decoration: none;
  }
  .play {
    position: absolute; left: 561px; top: 519px;
    width: 78px; height: 78px; border: 2px solid var(--ink); border-radius: 50%;
    display: flex; align-items: center; justify-content: center;
  }
  .footer {
    position: absolute; left: 0; top: 730px; width: 1200px; height: 64px;
    background: var(--footer);
  }
  .copyright {
    position: absolute; left: 0; right: 0; top: 23px; text-align: center;
    font-size: 12.4px; font-weight: 600;
  }
</style>
</head>
<body>
  <header class="hero">
    <div class="hero-photo" role="img" aria-label="Two-storey suburban home with lit gables, stone entry and trimmed hedges at dusk"></div>
    <div class="hero-veil"></div>
    <div class="brand">Fresh Dwelling Tract Guide</div>
    <div class="menu-toggle" aria-label="Menu">
      <svg width="16" height="14" viewBox="0 0 16 14"><rect y="0" width="16" height="3" fill="#fff"/><rect y="5.5" width="16" height="3" fill="#fff"/><rect y="11" width="16" height="3" fill="#fff"/></svg>
    </div>
    <section class="hero-content">
      <h1 class="hero-title">FRESH DWELLING TRACT GUIDE</h1>
      <p class="hero-sub">SED UT PERSPICIATIS UNDE OMNIS ISTE NATUS ERROR SIT VOLUPTATEM ACCUSANTIUM</p>
      <a class="cta" href="#">SEARCH FOR HOMES</a>
    </section>
    <div class="play" aria-label="Play video">
      <svg width="28" height="32" viewBox="0 0 28 32"><path d="M4 3 L25 16 L4 29 Z" fill="none" stroke="#fff" stroke-width="2.5" stroke-linejoin="round"/></svg>
    </div>
  </header>
  <footer class="footer">
    <p class="copyright">© Copyright-2018 Fresh Dwelling Tract Guide.All rights reserved.</p>
  </footer>
</body>
</html>
```